Veltrano.co - Polar Expeditions Specialists

We need a modern, visually striking business card for Veltrano.co, a company specialized in selling expedition cruises to the most remote regions on Earth, with a focus on the Arctic and Antarctica. The design should instantly communicate that the cardholder is an expert in polar travel. Use clean, premium aesthetics with cool tones like icy blue and white, possibly incorporating polar imagery (ice, glaciers, penguins, etc.)

Attached the logo

Contact Information for Business Card

Feels high-end and trustworthy.. Visually memorable — encourages people to keep it

Colors
0054AA
0677BA
7BADD7
CADEEF
E8F1F8

Requirements
Must have
• ice, glaciers, penguins, montains
Nice to have
• modern, transparente,

```html
<!DOCTYPE html>
<html lang="en">
<head>
<meta charset="utf-8">
<title>Veltrano.co – Business Card</title>
<link href="https://fonts.googleapis.com/css2?family=Poppins:wght@400;600;700&family=Arimo:wght@400&display=swap" rel="stylesheet">
<style>
  :root{
    --stage:#2e2e2e;
    --brand-blue:#3575b5;
    --brand-deep:#0054aa;
    --ice-mid:#7badd7;
    --ice-light:#cadeef;
    --ice-pale:#e8f1f8;
    --white:#ffffff;
    --ink:#3a3a3a;
    --muted:#8a8a8a;
  }
  *{margin:0;padding:0;box-sizing:border-box}
  html,body{width:1200px;height:689px;overflow:hidden;background:var(--stage)}
  .stage{width:1200px;height:689px;display:flex;align-items:center;justify-content:center;gap:44px}
  .card{width:536px;height:306px;border-radius:22px;position:relative;overflow:hidden;box-shadow:0 18px 40px rgba(0,0,0,.45)}
  .card--front{background:var(--brand-blue);display:flex;align-items:center;justify-content:center}
  .front-logo{display:flex;align-items:center;gap:18px}
  .logo-dot{width:52px;height:52px;border-radius:50%;background:var(--white);flex:none}
  .logo-text{font-family:'Poppins',sans-serif;color:var(--white)}
  .logo-name{font-weight:700;font-size:52px;line-height:1;letter-spacing:.5px}
  .logo-tagline{font-weight:600;font-size:15px;margin-top:6px;letter-spacing:.2px}

  .card--back{background:var(--white)}
  .back-artwork{position:absolute;left:0;bottom:0;width:300px;height:270px;
    background:linear-gradient(160deg,var(--brand-blue) 0%,var(--brand-blue) 55%,var(--ice-mid) 100%);
    border-top-right-radius:150px 130px}
  .back-info{position:absolute;left:300px;top:30px;right:20px}
  .back-name{font-family:'Poppins',sans-serif;font-weight:700;font-size:38px;color:var(--brand-blue);line-height:1}
  .back-tagline{font-family:'Poppins',sans-serif;font-weight:400;font-size:11.5px;color:var(--brand-blue);margin-top:4px}
  .person{margin-top:22px;font-family:'Poppins',sans-serif}
  .person-name{font-weight:600;font-size:19px;color:var(--brand-blue);line-height:1.1}
  .person-role{font-family:'Arimo',sans-serif;font-size:11px;color:var(--muted);margin-top:2px}
  .address{font-family:'Arimo',sans-serif;font-size:12px;color:var(--ink);margin-top:12px;line-height:1.35}
  .contacts{list-style:none;margin-top:12px;font-family:'Arimo',sans-serif;font-size:12px;color:var(--ink)}
  .contacts li{display:flex;align-items:center;gap:7px;line-height:1.45}
  .contacts svg{width:11px;height:11px;fill:var(--brand-blue);flex:none}
</style>
</head>
<body>
<main class="stage">
  <section class="card card--front">
    <div class="front-logo">
      <span class="logo-dot"></span>
      <div class="logo-text">
        <div class="logo-name">Veltrano.co</div>
        <div class="logo-tagline">Polar Expeditions Specialists</div>
      </div>
    </div>
  </section>

  <section class="card card--back">
    <div class="back-artwork" role="img" aria-label="Large blue silhouette artwork of a polar bear with two penguins and small stars"></div>
    <div class="back-info">
      <div class="back-name">Veltrano.co</div>
      <div class="back-tagline">Polar Expeditions Specialists</div>
      <div class="person">
        <div class="person-name">Mara Lindqvist</div>
        <div class="person-role">President</div>
      </div>
      <p class="address">4210 Glacier Bay Road<br>Whitehorse, Canada 51820</p>
      <ul class="contacts">
        <li><svg viewBox="0 0 24 24"><path d="M6.6 10.8a15.1 15.1 0 006.6 6.6l2.2-2.2a1 1 0 011-.25 11.4 11.4 0 003.6.57 1 1 0 011 1V20a1 1 0 01-1 1A17 17 0 013 4a1 1 0 011-1h3.5a1 1 0 011 1c0 1.25.2 2.45.57 3.6a1 1 0 01-.25 1z"/></svg>555-214-7780</li>
        <li><svg viewBox="0 0 24 24"><path d="M7 1h10a2 2 0 012 2v18a2 2 0 01-2 2H7a2 2 0 01-2-2V3a2 2 0 012-2zm0 3v14h10V4z"/></svg>555-309-6612</li>
        <li><svg viewBox="0 0 24 24"><path d="M2 5h20v14H2zm2 2v.5l8 5 8-5V7z"/></svg>info@veltrano.com</li>
        <li><svg viewBox="0 0 24 24"><circle cx="12" cy="12" r="10"/></svg>www.veltrano.com</li>
      </ul>
    </div>
  </section>
</main>
</body>
</html>
```